Create website for home automation - Control your lighting, fans, blinds etc remotely by smartphone

Plan for SHOPIFY Website - Our Clever Dwelling
Company name: Our Clever Dwelling
Company Slogan: Calm Evenings Come Naturally
Clean, Modern, Easy to Navigate, easy to maintain - not a lot of coding. We need flash technology but displaying simply what we do.
What we provide:
We will be offering wireless switch which can be added to iOS/Android App via WiFi, allowing users to remotely turn on/off connected lights, fans, security cameras, appliances, irrigation, humidifier separately from anywhere at any time.
Control your home away from home. No more wandering of your mind on those lights or appliances which you might have left switched on. No need to drive back home to check and switch them off. Save that energy, money and time just with a click of your phone no matter how far you are from home.
Replace your home electrical switches with smart switches. They retrofit existing electrical switches and allow you to make the transformation as needed.
Easy to use and intuitive app allows you to control your lights and devices just at a click. Set any kind of ambiance suiting your occasion.
Set scenes in smartphone app to group and operate your devices just at a button click. Same device can be included in more than one scene.
Collections and Products
Light Switches
Wall Plugs
Fan Switch
Pendants etc special lighting types.
Light Dimmers
Blind Controllers
Home Page:
Home page needs to telling customers what we do and how we do it in a few words to grab people.
Phone
Email
Support – Download instructions per product
Client login
Wholesale login
Promotional video to be on home screen - this is a short 1.5 - 2 min illustration introduction video to who we are and what we do - this is yet to be created)
Social media link - Facebook
Pages:
FAQ
About Us
Support/Shipping/Returns policy
Support/Installation
Blog posts
Product pages:
Description
Price
Space for where a video will be featured - how each product works/installation.
Reviews
Our competition:
http://www.brivo.com.au
https://lumigardenhub.com.au/2018/04/05/best-smart-light-switches-and-plugs/
https://www.tavelinq.com

```html
<!DOCTYPE html>
<html lang="en">
<head>
<meta charset="utf-8">
<title>Our Clever Dwelling – Latest Blog</title>
<link rel="stylesheet" href="https://fonts.googleapis.com/css2?family=Questrial&family=Open+Sans:wght@400;600&display=swap">
<style>
:root{
  --ink:#111111;
  --muted:#555555;
  --brand:#1d4a91;
  --brand-deep:#0f2f6e;
  --accent:#1760b8;
  --rule:#bdbdbd;
  --footer-bg:#0e0e0e;
  --footer-text:#e9e9e9;
  --footer-band:#1a5db4;
  --page:#ffffff;
}
*{box-sizing:border-box;margin:0;padding:0}
html,body{width:1200px;height:2546px;overflow:hidden;background:var(--page)}
body{position:relative;font-family:"Questrial",sans-serif;color:var(--ink)}

.site-header{position:absolute;left:0;top:0;width:1200px;height:150px;border-bottom:2px solid var(--rule)}
.brand{position:absolute;left:83px;top:40px;display:flex;align-items:center;gap:12px}
.brand-mark{width:34px;height:34px;background:var(--brand)}
.brand-name{display:block;font-size:22px;color:var(--brand-deep);letter-spacing:.3px}
.brand-slogan{display:block;font-size:11px;color:var(--accent);letter-spacing:1px;margin-top:3px}
.main-nav{position:absolute;left:382px;top:63px;display:flex;gap:0}
.main-nav a{font-size:20px;color:var(--ink);text-decoration:none;position:absolute;white-space:nowrap}
.main-nav a.is-current{color:var(--accent)}
.header-tools svg{position:absolute;top:66px}
.cart-count{position:absolute;left:1047px;top:60px;width:12px;height:12px;border-radius:50%;background:var(--accent);color:#fff;font:9px/12px "Open Sans",sans-serif;text-align:center}

.page-title{position:absolute;left:0;top:224px;width:1200px;text-align:center;font-size:48px;font-weight:400}

.blog-grid{position:absolute;left:87px;top:385px;display:grid;grid-template-columns:472px 472px;column-gap:77px;row-gap:0}
.post{height:543px}
.post-media{position:relative;height:280px}
.post-image{width:472px;height:280px}
.post-date{position:absolute;right:0;top:0;width:156px;height:39px;background:var(--brand);color:#fff;font-size:20px;line-height:39px;text-align:center}
.post-title{font-size:23px;font-weight:400;margin-top:20px;line-height:1.3}
.post-excerpt{font-family:"Open Sans",sans-serif;font-size:15px;line-height:26.5px;color:var(--muted);margin-top:8px}
.post-more{display:inline-block;margin-top:10px;font-family:"Open Sans",sans-serif;font-weight:600;font-size:16px;color:var(--brand-deep);text-decoration:none}

.load-more{position:absolute;left:529px;top:2048px;width:143px;height:41px;border-radius:12px;background:var(--accent);color:#fff;font-family:"Open Sans",sans-serif;font-size:20px;line-height:41px;text-align:center;box-shadow:0 2px 5px rgba(0,0,0,.3)}

.site-footer{position:absolute;left:0;top:2201px;width:1200px;height:345px;background:var(--footer-bg);border-top:10px solid var(--footer-band);color:var(--footer-text);font-family:"Open Sans",sans-serif}
.footer-col{position:absolute;top:76px}
.footer-heading{font-size:16px;font-weight:400;letter-spacing:.3px;margin-bottom:22px}
.footer-list{list-style:none;font-size:13.5px;line-height:24px}
.footer-list li::before{content:"» ";}
.contact-lines{font-size:13.5px;line-height:23px;padding-left:4px}
.contact-lines p+p{margin-top:12px}
.social{display:flex;gap:13px;margin-top:30px}
.social span{width:26px;height:26px;border-radius:4px;background:var(--footer-text)}
.footer-rule{position:absolute;left:92px;right:92px;top:258px;border-top:1px solid #2a2a2a}
.copyright{position:absolute;left:0;width:1200px;top:291px;text-align:center;font-size:14px}
</style>
</head>
<body>

<header class="site-header">
  <div class="brand">
    <span class="brand-mark"></span>
    <span>
      <span class="brand-name">Our Clever Dwelling</span>
      <span class="brand-slogan">Calm Evenings Come Naturally</span>
    </span>
  </div>
  <nav class="main-nav">
    <a style="left:0">Home</a>
    <a style="left:76px">About Us</a>
    <a style="left:183px">Products</a>
    <a style="left:287px">Support</a>
    <a style="left:383px" class="is-current">Blog</a>
    <a style="left:453px">FAQ</a>
    <a style="left:519px">Contact</a>
  </nav>
  <div class="header-tools">
    <svg style="left:1003px" width="18" height="18" viewBox="0 0 18 18" aria-label="Search"><circle cx="7.5" cy="7.5" r="5.5" fill="none" stroke="#111" stroke-width="2.6"/><line x1="11.5" y1="11.5" x2="16.5" y2="16.5" stroke="#111" stroke-width="3" stroke-linecap="round"/></svg>
    <svg style="left:1042px" width="20" height="18" viewBox="0 0 20 18" aria-label="Cart"><path d="M1 6h18l-2.5 11h-13z" fill="#111"/><path d="M6 6l4-5 4 5" fill="none" stroke="#111" stroke-width="1.6"/></svg>
    <span class="cart-count">1</span>
    <svg style="left:1089px" width="18" height="18" viewBox="0 0 18 18" aria-label="Account"><circle cx="9" cy="5" r="4.5" fill="#111"/><path d="M0 18c0-6 4-8 9-8s9 2 9 8z" fill="#111"/></svg>
  </div>
</header>

<h1 class="page-title">Latest Blog</h1>

<main class="blog-grid">
  <article class="post">
    <div class="post-media">
      <div class="post-image" role="img" aria-label="Hand holding a smartphone with a home control app in a bright living room" style="background:linear-gradient(120deg,#8a6a4a,#d8c7b0 45%,#5d5a5c 80%,#b39580)"></div>
      <span class="post-date">NOV 04, 2018</span>
    </div>
    <h2 class="post-title">Neque porro quisquam est qui dolorem</h2>
    <p class="post-excerpt">The point of using Lorem Ipsum is that it has a more-or-less normal distribution of letters, as opposed to using 'Content here, content here', making it look like readable English. Many desktop publishing packages and web page editors.</p>
    <a class="post-more">Read more...</a>
  </article>
  <article class="post">
    <div class="post-media">
      <div class="post-image" role="img" aria-label="Hands holding a tablet showing a smart home dashboard" style="background:linear-gradient(135deg,#8f9aa8,#3f5a7d 40%,#15304f 60%,#6e7e92)"></div>
      <span class="post-date">NOV 04, 2018</span>
    </div>
    <h2 class="post-title">Neque porro quisquam est qui dolorem</h2>
    <p class="post-excerpt">The point of using Lorem Ipsum is that it has a more-or-less normal distribution of letters, as opposed to using 'Content here, content here', making it look like readable English. Many desktop publishing packages and web page editors.</p>
    <a class="post-more">Read more...</a>
  </article>
  <article class="post">
    <div class="post-media">
      <div class="post-image" role="img" aria-label="Tablet with device control icons floating around it in a warm room" style="background:linear-gradient(120deg,#6a4a36,#b89b83 45%,#6c5a8c 65%,#8a6d55)"></div>
      <span class="post-date">NOV 04, 2018</span>
    </div>
    <h2 class="post-title">Neque porro quisquam est qui dolorem</h2>
    <p class="post-excerpt">The point of using Lorem Ipsum is that it has a more-or-less normal distribution of letters, as opposed to using 'Content here, content here', making it look like readable English. Many desktop publishing packages and web page editors.</p>
    <a class="post-more">Read more...</a>
  </article>
  <article class="post">
    <div class="post-media">
      <div class="post-image" role="img" aria-label="Smartphone connected to a network of home appliance icons" style="background:linear-gradient(120deg,#7c8a4e,#c9d3b0 45%,#9fb8b0 70%,#e3e8dd)"></div>
      <span class="post-date">NOV 04, 2018</span>
    </div>
    <h2 class="post-title">Neque porro quisquam est qui dolorem</h2>
    <p class="post-excerpt">The point of using Lorem Ipsum is that it has a more-or-less normal distribution of letters, as opposed to using 'Content here, content here', making it look like readable English. Many desktop publishing packages and web page editors.</p>
    <a class="post-more">Read more...</a>
  </article>
  <article class="post">
    <div class="post-media">
      <div class="post-image" role="img" aria-label="Hands using a tablet home control screen in a lamp-lit room" style="background:linear-gradient(120deg,#6e3a22,#c07a44 40%,#3a2a2e 65%,#8a3a3e)"></div>
      <span class="post-date">NOV 04, 2018</span>
    </div>
    <h2 class="post-title">Neque porro quisquam est qui dolorem</h2>
    <p class="post-excerpt">The point of using Lorem Ipsum is that it has a more-or-less normal distribution of letters, as opposed to using 'Content here, content here', making it look like readable English. Many desktop publishing packages and web page editors.</p>
    <a class="post-more">Read more...</a>
  </article>
  <article class="post">
    <div class="post-media">
      <div class="post-image" role="img" aria-label="Finger touching a glowing house icon surrounded by smart home symbols" style="background:linear-gradient(120deg,#5c6a80,#2c3c58 45%,#8896ac 70%,#4a5870)"></div>
      <span class="post-date">NOV 04, 2018</span>
    </div>
    <h2 class="post-title">Neque porro quisquam est qui dolorem</h2>
    <p class="post-excerpt">The point of using Lorem Ipsum is that it has a more-or-less normal distribution of letters, as opposed to using 'Content here, content here', making it look like readable English. Many desktop publishing packages and web page editors.</p>
    <a class="post-more">Read more...</a>
  </article>
</main>

<a class="load-more">Load More</a>

<footer class="site-footer">
  <div class="footer-col" style="left:92px">
    <h3 class="footer-heading">INFORMATION</h3>
    <ul class="footer-list"><li>Privacy Policy</li><li>Your Account</li><li>Advanced Search</li><li>Contact Us</li></ul>
  </div>
  <div class="footer-col" style="left:358px">
    <h3 class="footer-heading">LINKS</h3>
    <ul class="footer-list"><li>Home</li><li>About us</li><li>Products</li><li>Shop</li></ul>
  </div>
  <div class="footer-col" style="left:562px">
    <h3 class="footer-heading">CONTACT US</h3>
    <div class="contact-lines">
      <p>Address : 48-52 Harwick - Ellmore Road,<br>Ellmore, Canada</p>
      <p>Phone :&nbsp; (03) 5550 2417,&nbsp; (04) 5550 7381</p>
      <p>Email : sales@cleverdwelling.example</p>
    </div>
  </div>
  <div class="footer-col" style="left:925px;top:70px">
    <h3 class="footer-heading" style="margin-bottom:0">FOLLOW US OUT THERE</h3>
    <div class="social"><span></span><span></span><span></span><span></span></div>
  </div>
  <div class="footer-rule"></div>
  <p class="copyright">Copyright © 2018. All Rights Reserved</p>
</footer>

</body>
</html>
```